Business card for builder specialising in renovations.

Need a card for our building business. Business name is under Martin Powles.
Have licence number on card ( 527691K)
Contact number (0400 382 415)
Want to work on logo for some business cards and shirts - something with MP or MPB or open to ideas??
No animations, No hammers. Something sharp and eye catching.
Highlight that we are a renovation specialist. Simple on front with extra details on back with some lines to jot down things.

Target Market(s)

Renovators

Industry/Entity Type

Building

Contact Information for Business Card

2 sided with room on back to jot things down.
Extra details on back so front can be simple ..like, renovations, bathrooms, decks, extensions, new builds,

Logo Text

MP

Font styles to use
Serif

Requirements
Must have
• Eye catching design .
• Name : Martin powles
• Licence number
• Contact number - 0400382415
Nice to have
• Some logo design that we can carry through to other forms of advertising
• Local builder
• Quality work
Should not have
• No animations

```html
<!DOCTYPE html>
<html lang="en">
<head>
<meta charset="utf-8">
<title>Martin Powles – Business Card</title>
<link rel="stylesheet" href="https://fonts.googleapis.com/css2?family=Open+Sans:wght@400;600;700&display=swap">
<style>
  :root {
    --backdrop: #2b2623;
    --card: #0c0c0d;
    --card-edge: #1a1a1b;
    --brand-blue: #1c9fd8;
    --brand-grey: #9a9a9a;
    --text-light: #f2f2f2;
  }
  html, body {
    margin: 0;
    padding: 0;
    width: 1200px;
    height: 844px;
    overflow: hidden;
    background: var(--backdrop);
    font-family: "Open Sans", Arial, sans-serif;
  }
  .canvas {
    position: relative;
    width: 1200px;
    height: 844px;
  }
  .card {
    position: absolute;
    width: 540px;
    height: 310px;
    background: var(--card);
    border: 1px solid var(--card-edge);
    box-shadow: 0 10px 30px rgba(0,0,0,.55);
    overflow: hidden;
  }
  .card--front { left: 60px; top: 440px; }
  .card--back  { left: 600px; top: 100px; }

  .wordmark {
    display: flex;
    align-items: center;
    gap: 14px;
    font-weight: 600;
    color: var(--brand-blue);
    white-space: nowrap;
  }
  .wordmark__square {
    background: var(--brand-blue);
    flex: none;
  }
  .card--front .wordmark {
    position: absolute;
    left: 40px;
    top: 110px;
    font-size: 38px;
  }
  .card--front .wordmark__square { width: 40px; height: 40px; }

  .divider {
    position: absolute;
    left: 0;
    top: 200px;
    width: 510px;
    height: 1.5px;
    background: var(--brand-blue);
  }

  .contact {
    position: absolute;
    right: 30px;
    top: 160px;
    text-align: right;
    line-height: 1;
  }
  .contact__name {
    font-size: 20px;
    font-weight: 600;
    color: var(--brand-blue);
  }
  .contact__name .surname { color: var(--brand-grey); }
  .contact__phone {
    margin-top: 22px;
    font-size: 15px;
    color: var(--text-light);
    display: flex;
    justify-content: flex-end;
    align-items: center;
    gap: 6px;
  }
  .contact__phone svg { width: 12px; height: 12px; }
  .contact__licence {
    margin-top: 14px;
    font-size: 15px;
    font-weight: 600;
    color: var(--text-light);
  }

  .card--back .wordmark {
    position: absolute;
    left: 0;
    right: 0;
    top: 105px;
    justify-content: center;
    font-size: 34px;
  }
  .card--back .wordmark__square { width: 34px; height: 34px; }
  .services {
    position: absolute;
    left: 30px;
    right: 30px;
    bottom: 58px;
    font-size: 14px;
    font-weight: 600;
    color: var(--text-light);
    text-align: center;
  }
</style>
</head>
<body>
<main class="canvas">
  <section class="card card--front" aria-label="Card front">
    <div class="wordmark">
      <span class="wordmark__square"></span>
      <span class="wordmark__name">Martin Powles</span>
    </div>
    <div class="divider"></div>
    <div class="contact">
      <div class="contact__name">Martin <span class="surname">Powles</span></div>
      <div class="contact__phone">
        <span>0400 382 415</span>
        <svg viewBox="0 0 24 24" aria-hidden="true"><path fill="#1c9fd8" d="M6.6 10.8a15.1 15.1 0 0 0 6.6 6.6l2.2-2.2c.3-.3.7-.4 1-.2 1.1.4 2.3.6 3.6.6.6 0 1 .4 1 1V20c0 .6-.4 1-1 1A17 17 0 0 1 3 4c0-.6.4-1 1-1h3.5c.6 0 1 .4 1 1 0 1.3.2 2.5.6 3.6.1.3 0 .7-.2 1z"/></svg>
      </div>
      <div class="contact__licence">License No- 527691K</div>
    </div>
  </section>

  <section class="card card--back" aria-label="Card back">
    <div class="wordmark">
      <span class="wordmark__square"></span>
      <span class="wordmark__name">Martin Powles</span>
    </div>
    <p class="services">Rrenovations, bathrooms, decks, extensions, new builds etc</p>
  </section>
</main>
</body>
</html>
```